Therapeutic Counselling Practice Brochure

I have a new therapeutic counselling practice in Melbourne.

I am making peri natal issues my special interest area.

I need a brochure targeted at new parents or pregnant women and partners, struggling with the concept of parenting, depression, maybe do not even know about it.

The feel should be safe and strong. I love the WREN website ( I do volunteer work with them)

Out of hours appointments and telephone counselling are important making my service very accessible.

Attached is an example for the content of the Brochure

Attached is an example for the content of the Brochure.

Target Market(s)

25 - 45 New Parents , expectant parents,families and friends of people struggling emotionally and mentally with and around being new parents

Requirements
Must have
• Feel of safety, somewhere to go for help, support, a conversation, soft ,strong
Nice to have
• mother and child, maybe parents and child, possibly a graphic, faceless

```html
<!DOCTYPE html>
<html lang="en">
<head>
<meta charset="utf-8">
<title>Marian Holloway – Counsellor and Personal Coach</title>
<link rel="stylesheet" href="https://fonts.googleapis.com/css2?family=Open+Sans:ital,wght@0,400;0,600;0,700;1,400;1,700&family=Arimo:ital,wght@1,400;1,700&display=swap">
<style>
  :root {
    --green-dark: #3e6b2c;
    --green-mid: #5d8c38;
    --green-light: #9cc954;
    --green-pale: #e3efcf;
    --text: #2b2b2b;
    --white: #ffffff;
  }
  * { box-sizing: border-box; margin: 0; padding: 0; }
  html, body { width: 1200px; height: 854px; overflow: hidden; background: var(--white); }
  .brochure {
    position: relative; width: 1200px; height: 854px; overflow: hidden;
    font-family: "Open Sans", Arial, sans-serif; color: var(--text); background: var(--white);
  }
  .panel { position: absolute; top: 0; height: 854px; }
  .panel--left { left: 0; width: 400px; }
  .panel--middle { left: 400px; width: 395px; }
  .panel--right { left: 795px; width: 405px; background: var(--green-dark); }

  .waves { position: absolute; left: 0; top: 0; width: 1200px; height: 854px; pointer-events: none; }

  /* left panel */
  .hero-silhouette {
    position: absolute; left: 170px; top: 0; width: 230px; height: 160px;
    background:
      linear-gradient(90deg, #ffffff 0%, rgba(255,255,255,0) 45%),
      linear-gradient(180deg, #d8b27a 0%, #8a6a44 45%, #3a2f25 100%);
  }
  .feature-title { position: absolute; left: 42px; top: 30px; color: var(--green-dark); line-height: 1.18; }
  .feature-title .big { font-size: 34px; font-weight: 700; letter-spacing: 0.3px; display: block; }
  .feature-title .line { font-size: 26px; font-weight: 400; letter-spacing: -0.4px; display: block; }
  .feature-title strong { font-weight: 700; }
  .feature-body { position: absolute; left: 42px; top: 202px; width: 326px; font-size: 13.4px; line-height: 20px; text-align: justify; }
  .feature-body p { margin-bottom: 11px; }
  .feature-body p.tight { margin-bottom: 0; }
  .feature-body .squeeze { letter-spacing: -0.3px; }
  .stat { color: var(--green-mid); font-weight: 700; }
  .source { float: right; font-size: 11px; margin-top: 1px; }

  /* middle panel */
  .portrait {
    position: absolute; left: 20px; top: 0; width: 375px; height: 255px;
    background: linear-gradient(90deg, #efe6d6 0%, #d7c0a2 45%, #7da25a 80%, #4c7a2e 100%);
  }
  .name-tab {
    position: absolute; left: 0; top: 248px; width: 395px; height: 32px;
    background: linear-gradient(90deg, var(--green-light) 0%, var(--green-pale) 55%, var(--white) 100%);
    clip-path: polygon(0 35%, 12% 0, 100% 0, 100% 100%, 12% 100%, 0 100%);
  }
  .name-tab span { position: absolute; left: 70px; top: 4px; font-size: 17px; font-weight: 700; color: var(--text); }
  .contact { position: absolute; left: 35px; top: 296px; width: 325px; font-size: 14.5px; line-height: 20px; }
  .contact p { margin-bottom: 20px; }
  .contact .italic { font-style: italic; }
  .contact .callout { text-align: center; font-style: italic; font-weight: 700; margin-bottom: 16px; }
  .booking { text-align: center; font-size: 14px; line-height: 20px; }
  .booking strong { font-weight: 700; }

  /* right panel */
  .brand { position: absolute; left: 22px; top: 40px; display: flex; align-items: flex-start; gap: 14px; }
  .brand-dot { width: 60px; height: 60px; border-radius: 50%; border: 3px solid var(--white); margin-top: 2px; }
  .brand-name { color: var(--white); font-weight: 700; font-size: 24px; line-height: 1.1; }
  .brand-role { color: var(--white); font-weight: 700; font-size: 14.5px; margin-top: 4px; }
  .mother-baby {
    position: absolute; left: 0; top: 95px; width: 405px; height: 405px;
    background: linear-gradient(135deg, #f7ece4 0%, #e8c3a6 40%, #f2d9c8 70%, #ffffff 100%);
    clip-path: path("M0 55 C120 10 260 -5 405 0 L405 405 L0 405 Z");
  }
  .right-lower { position: absolute; left: 0; top: 500px; width: 405px; height: 354px; background: var(--white); }
  .invite { position: absolute; left: 28px; top: 522px; color: var(--green-dark); }
  .invite h2 { font-size: 29px; font-weight: 700; line-height: 1.25; letter-spacing: 0.5px; }
  .invite h2 .big { font-size: 32px; }
  .invite h3 { font-family: "Arimo", Arial, sans-serif; font-style: italic; font-weight: 700; font-size: 23px; color: var(--green-mid); margin-top: 2px; }
  .invite-text {
    position: absolute; left: 30px; top: 637px; width: 275px;
    font-family: "Arimo", Arial, sans-serif; font-style: italic; font-weight: 700;
    font-size: 15px; line-height: 19.5px; color: var(--green-mid);
  }
</style>
</head>
<body>
<main class="brochure">
  <section class="panel panel--left">
    <div class="hero-silhouette" role="img" aria-label="Silhouette of a father holding his baby against a sunset sky"></div>
    <h1 class="feature-title">
      <span class="big">DEPRESSION</span>
      <span class="line">in <strong>Men</strong> after the</span>
      <span class="line"><strong>Birth</strong> of their <strong>Baby</strong></span>
    </h1>
    <div class="feature-body">
      <p>Becoming a father can be difficult to cope with and some men feel they have nowhere to turn for support.</p>
      <p>According to recent research, about <span class="stat">10 per cent of new fathers</span> become depressed after the birth of their child. <span class="source">www.dadsupport.org</span></p>
      <p class="tight">Having a new baby is a huge change, involving physical exhaustion and extra worries.</p>
      <p>It can be particularly difficult to balance the demands of work and fatherhood, especially as you might feel under pressure to earn more while your partner is not able to work.</p>
      <p>For new parents the focus of attention will have shifted and this can feel like a loss as well as a gain.</p>
      <p class="tight squeeze">Some men report feeling overwhelmed, isolated and confused by their feelings and their partner's reaction to them. They are often irritable, aggressive and sometimes hostile.</p>
      <p class="tight squeeze">Symptoms can include feeling very low - for example, not enjoying anything, poor concentration, perhaps a poor appetite and worrying at night.</p>
      <p>Some men feel ashamed of their feelings and experiences and this makes it very difficult for them to seek out and receive help.</p>
      <p>Counselling can help, being able to talk openly and honestly in a safe and confidential space.</p>
    </div>
  </section>

  <section class="panel panel--middle">
    <div class="portrait" role="img" aria-label="Portrait of the counsellor among green leaves"></div>
    <div class="name-tab"><span>Marian Holloway J.P.</span></div>
    <div class="contact">
      <p><strong>Office:</strong><br>Level 2, 118 Linden Street,<br>Southbank 3006</p>
      <p class="italic">Evening and weekend appointments available.</p>
      <p><strong>Telephone Counselling</strong> saves travel time and the hassle of parking.</p>
      <p>Telephone counselling gives you a convenient option in accessing therapy.</p>
      <p>Some people feel more comfortable discussing issues over the telephone, still within the safe supportive and confidential framework.</p>
      <p class="callout">Telephone appointments are usually<br>available within 48 hours.</p>
      <div class="booking">
        To book please contact<br>
        <strong>Marian Holloway</strong><br>
        on <strong>0400 555 318</strong><br>
        <strong>marian@marianholloway.com.au</strong><br>
        <strong>www.marianholloway.com.au</strong>
      </div>
    </div>
  </section>

  <section class="panel panel--right">
    <div class="mother-baby" role="img" aria-label="Mother cuddling her smiling baby"></div>
    <div class="brand">
      <span class="brand-dot"></span>
      <div>
        <div class="brand-name">Marian Holloway</div>
        <div class="brand-role">Counsellor and Personal Coach</div>
      </div>
    </div>
    <div class="right-lower"></div>
    <div class="invite">
      <h2>ARE YOU EXPECTING<br>OR A <span class="big">NEW PARENT</span>?</h2>
      <h3>Got the “Baby Blues”?</h3>
    </div>
    <p class="invite-text">There is an expectation of happiness and fulfilment around childbirth.<br>Feeling “blue”, interferes with the adjustment to becoming a parent.<br>Sharing your feelings by talking is important.</p>
  </section>

  <svg class="waves" viewBox="0 0 1200 854" aria-hidden="true">
    <path d="M0 160 L400 160 L400 190 L35 190 L0 210 Z" fill="#e9f2da"/>
    <path d="M0 165 L35 190 L0 210 Z" fill="#9cc954"/>
    <path d="M0 790 C300 845 650 845 795 820 L795 854 L0 854 Z" fill="#9cc954" opacity="0.55"/>
    <path d="M0 822 C350 860 650 850 795 835 L795 854 L0 854 Z" fill="#8bbd45"/>
    <path d="M420 808 C600 818 720 815 795 808" stroke="#e3efcf" stroke-width="6" fill="none"/>
    <path d="M795 520 C950 470 1100 420 1200 330 L1200 400 C1100 470 950 510 795 530 Z" fill="#9cc954" opacity="0.6"/>
    <path d="M795 815 C1000 800 1150 730 1200 655 L1200 854 L795 854 Z" fill="#9cc954" opacity="0.6"/>
    <path d="M795 854 C1000 845 1150 790 1200 745 L1200 854 Z" fill="#5d8c38"/>
  </svg>
</main>
</body>
</html>
```